Brightarc Orthodontics appointment card design

I need appointment cards/ business cards made. Front will be Logo, name, title, email, phone number and location (5263 Walnut Hollow Pkwy, Ste 412, Concord, NC 28027) . the back should have an appointment card (name, time, date) and also 3 addresses listed with a check box so we can check to which location they are going.
Dale Fenwick Orthodontics
- 6735 Orchard Street, Ste 514, Harrisburg, NC 28075
- 3647 Ridgeway Drive NE, Ste 810, Concord, NC 28025
- 2917 Thornbury Corporate Drive, Ste 605, Charlotte, NC 28277
Business card can be horizontal or vertical in Design.
I need to be able to edit it to update and add new employees

Requirements
Must have
• Front:
• - Logo
• - Name & Title (able to be edited)
• - phone (704-555-0186) & Email (need to be able to edit)
• - Address: 5263 Walnut Hollow Pkwy, Ste 412
• Concord, NC 28027
• Back:
• Appointment Card design:
• - Name, time, Date
• - 3 locations w/ a check box so the patient knows where to go:
• Dale Fenwick Orthodontics
• - 6735 Orchard Street, Ste 514, Harrisburg, NC 28075
• - 3647 Ridgeway Drive NE, Ste 810, Concord, NC 28025
• - 2917 Thornbury Corporate Drive, Ste 605, Charlotte, NC 28277

```html
<!DOCTYPE html>
<html lang="en">
<head>
<meta charset="utf-8">
<title>Brightarc Orthodontics – Business &amp; Appointment Card</title>
<link rel="stylesheet" href="https://fonts.googleapis.com/css2?family=Poppins:wght@400;500;600;700&display=swap">
<style>
  :root {
    --bg: #2a2d31;
    --card: #ffffff;
    --blue: #1f74b8;
    --blue-deep: #125a97;
    --blue-faint: #e6eef6;
    --grey: #6f7378;
    --line: #9a9ea3;
    --white: #ffffff;
  }
  * { box-sizing: border-box; margin: 0; padding: 0; }
  html, body { width: 1200px; height: 900px; overflow: hidden; }
  body {
    background: var(--bg);
    font-family: "Poppins", sans-serif;
    position: relative;
  }
  .card {
    position: absolute;
    top: 302px;
    width: 520px;
    height: 297px;
    background: var(--card);
    border-radius: 24px;
    overflow: hidden;
  }
  .card--front { left: 60px; }
  .card--back  { left: 620px; }

  /* Front */
  .front-wave { position: absolute; inset: 0; }
  .holder { position: absolute; left: 30px; top: 28px; }
  .holder__name { font-weight: 700; font-size: 19px; color: var(--blue-deep); letter-spacing: .5px; }
  .holder__title { font-size: 10px; color: var(--grey); letter-spacing: 1px; }
  .brand {
    position: absolute; right: 30px; top: 86px;
    display: flex; align-items: center; gap: 10px;
  }
  .brand__dot { width: 14px; height: 14px; border-radius: 50%; background: var(--blue); }
  .brand__name { font-weight: 600; font-size: 22px; color: var(--blue); }
  .contact {
    position: absolute; left: 30px; top: 172px;
    color: var(--white); font-size: 12.5px; line-height: 1.55;
  }
  .address {
    position: absolute; right: 28px; bottom: 20px;
    color: var(--white); font-size: 13px; line-height: 1.4; text-align: right;
  }

  /* Back */
  .watermark {
    position: absolute; right: 22px; top: 8px;
    font-weight: 700; font-size: 96px; color: var(--blue-faint);
    line-height: 1;
  }
  .field {
    position: absolute; display: flex; align-items: flex-end; gap: 8px;
    color: var(--blue); font-size: 12px;
  }
  .field__rule { flex: 1; border-bottom: 1px solid var(--line); height: 1px; margin-bottom: 3px; }
  .field--name { left: 26px; right: 26px; top: 24px; }
  .field--time { left: 26px; width: 250px; top: 62px; }
  .field--date { left: 290px; right: 26px; top: 62px; }
  .practice {
    position: absolute; left: 0; right: 0; top: 104px;
    text-align: center; font-weight: 700; font-size: 13px; color: var(--blue); letter-spacing: .5px;
  }
  .locations {
    position: absolute; left: 0; right: 0; top: 138px; height: 130px;
    background: var(--blue);
    display: grid; grid-template-columns: repeat(3, 1fr);
    padding: 0 18px;
  }
  .location { position: relative; padding-top: 26px; color: var(--white); font-size: 11px; line-height: 1.4; }
  .location__check {
    position: absolute; top: -13px; left: 4px;
    width: 26px; height: 26px; border-radius: 50%;
    background: var(--white); border: 2px solid var(--blue-deep);
  }
</style>
</head>
<body>

<section class="card card--front" aria-label="Business card front">
  <svg class="front-wave" viewBox="0 0 520 297" width="520" height="297" aria-hidden="true">
    <path d="M0,112 C120,104 200,168 300,208 C380,240 450,250 520,246 L520,297 L0,297 Z" fill="var(--blue-deep)"/>
    <path d="M0,126 C120,120 200,184 300,224 C380,256 450,264 520,260 L520,297 L0,297 Z" fill="var(--blue)"/>
  </svg>
  <div class="holder">
    <p class="holder__name">JOHANTHAN DOE</p>
    <p class="holder__title">TITLE</p>
  </div>
  <div class="brand">
    <span class="brand__dot"></span>
    <span class="brand__name">Brightarc Orthodontics</span>
  </div>
  <div class="contact">
    <p>704-555-0186</p>
    <p>name@brightarcortho.com</p>
    <p>www.brightarcortho.com</p>
  </div>
  <p class="address">5263 Walnut Hollow Pkwy<br>Ste 412, Concord, NC 28027</p>
</section>

<section class="card card--back" aria-label="Appointment card back">
  <p class="watermark" aria-hidden="true">Brightarc</p>
  <div class="field field--name"><span>Name</span><span class="field__rule"></span></div>
  <div class="field field--time"><span>Time</span><span class="field__rule"></span></div>
  <div class="field field--date"><span>Date</span><span class="field__rule"></span></div>
  <p class="practice">DALE FENWICK ORTHODONTICS</p>
  <div class="locations">
    <div class="location">
      <span class="location__check"></span>
      6735 Orchard Street<br>Ste 514, Harrisburg<br>NC 28075
    </div>
    <div class="location">
      <span class="location__check"></span>
      2917 Thornbury Corporate<br>Drive, Ste 605, Charlotte<br>NC 28277
    </div>
    <div class="location">
      <span class="location__check"></span>
      3647 Ridgeway Drive NE<br>Ste 810, Concord<br>NC 28025
    </div>
  </div>
</section>

</body>
</html>
```